New Zealand Marlborough Sauvignon Blanc wine packaging design

We need packaging design for our new wine brand, Dunmore Vale. The wine is a New Zealand Marlborough Sauvignon Blanc. We would like the packaging will portray elegance and style with an understated label. We are looking for a label that portrays the elegance of the French Riviera. The label should be round or pill shaped.
Updates

Industry/Entity Type

Wine

Font styles to use
Serif
Sans Serif

Requirements
Must have
• The words in order of importance: Dunmore Vale, Sauvignon Blanc, Marlborough, New Zealand. It should be fit to the bottle posted in the links
Nice to have
• a pill shape or circular shape
Should not have
• Illustrations of wine bottles, wine glasses, or grapes

```html
<!DOCTYPE html>
<html lang="en">
<head>
<meta charset="utf-8">
<title>Dunmore Vale Sauvignon Blanc Label</title>
<link rel="stylesheet" href="https://fonts.googleapis.com/css2?family=Pinyon+Script&family=Jost:wght@400;500&display=swap">
<style>
  :root {
    --bg: #d5e9dc;
    --label-white: #ffffff;
    --sky-light: #b5d9bf;
    --mint: #7cc6b1;
    --teal: #2a9a9c;
    --deep-teal: #1c7a8a;
    --night-blue: #13536f;
    --ink-light: #ffffff;
  }
  html, body {
    margin: 0;
    padding: 0;
    width: 1200px;
    height: 675px;
    overflow: hidden;
    background: var(--bg);
  }
  .canvas {
    position: relative;
    width: 1200px;
    height: 675px;
    background: var(--bg);
  }
  .label {
    position: absolute;
    left: 410px;
    top: 58px;
    width: 380px;
    height: 558px;
  }
  .label-shape {
    position: absolute;
    inset: 0;
    width: 380px;
    height: 558px;
  }
  .rule {
    position: absolute;
    height: 1px;
    background: var(--ink-light);
    opacity: 0.85;
  }
  .rule--top { left: 74px; width: 232px; top: 216px; }
  .rule--bottom { left: 74px; width: 232px; top: 328px; }
  .rule--divider { left: 174px; width: 32px; top: 402px; }
  .brand-name {
    position: absolute;
    margin: 0;
    font-family: "Pinyon Script", cursive;
    font-weight: 400;
    color: var(--ink-light);
    font-size: 60px;
    line-height: 1;
    white-space: nowrap;
  }
  .brand-name__first { left: 76px; top: 208px; }
  .brand-name__second { left: 158px; top: 264px; }
  .varietal {
    position: absolute;
    left: 0;
    width: 380px;
    top: 349px;
    margin: 0;
    text-align: center;
    font-family: "Jost", sans-serif;
    font-weight: 500;
    font-size: 12.5px;
    letter-spacing: 0.64em;
    text-indent: 0.64em;
    color: var(--ink-light);
    white-space: nowrap;
  }
  .origin {
    position: absolute;
    left: 0;
    width: 380px;
    top: 430px;
    margin: 0;
    text-align: center;
    font-family: "Pinyon Script", cursive;
    font-size: 20px;
    color: var(--ink-light);
    white-space: nowrap;
  }
</style>
</head>
<body>
<main class="canvas">
  <section class="label" aria-label="Dunmore Vale Sauvignon Blanc wine label">
    <svg class="label-shape" viewBox="0 0 770 1130" xmlns="http://www.w3.org/2000/svg">
      <defs>
        <clipPath id="pill">
          <path d="M0 385 A385 385 0 0 1 770 385 L770 745 A385 385 0 0 1 0 745 Z"/>
        </clipPath>
        <linearGradient id="valley" x1="0" y1="0" x2="0" y2="1130" gradientUnits="userSpaceOnUse">
          <stop offset="0" stop-color="var(--sky-light)"/>
          <stop offset="0.3" stop-color="var(--mint)"/>
          <stop offset="0.45" stop-color="var(--teal)"/>
          <stop offset="0.6" stop-color="var(--deep-teal)"/>
          <stop offset="0.7" stop-color="var(--night-blue)"/>
          <stop offset="1" stop-color="var(--night-blue)"/>
        </linearGradient>
      </defs>
      <g clip-path="url(#pill)">
        <rect class="label-band" x="0" y="0" width="770" height="1130" fill="var(--label-white)"/>
        <path class="label-scene" role="img" aria-label="Misty mountain landscape illustration under a glowing sun"
              d="M0 610 L0 330 L63 330 A330 330 0 0 1 707 330 L770 330 L770 1130 L0 1130 Z"
              fill="url(#valley)"/>
      </g>
    </svg>
    <span class="rule rule--top"></span>
    <h1 class="brand-name brand-name__first">Dunmore</h1>
    <span class="brand-name brand-name__second">Vale</span>
    <span class="rule rule--bottom"></span>
    <p class="varietal">SAUVIGNON BLANC</p>
    <span class="rule rule--divider"></span>
    <p class="origin">Marlborough - New Zealand</p>
  </section>
</main>
</body>
</html>
```